real esate business card with company logo and name

we need a business card design for a real esate company

The company name is Walsh & Brand Pty Ltd, and we have our logo designed and will upload. We want classic or moden feel. Black or white background. looks more textured. Should include folowinginformations
Owen Walsh and Lucy Brand
Sales Agents & Onsite Manager
p: 07 5948 2063
F: 07 5948 2174
M:0431 857 219
3/42 Marlow Crescent, FERNLEA QLD 4213

We want this business card looks professonal. Thank you in advance.

Industry/Entity Type

Real Estate Agent

Contact Information for Business Card

Owen Walsh and Lucy Brand
Onsite Manager & Sales Agents
p: 07 5948 2063
M:0431 857 219

Font styles to use
Serif

Colors
000000
fbfbfb
333333
959595

Requirements
Must have
• company logo and name, black or white back ground

```html
<!DOCTYPE html>
<html lang="en">
<head>
<meta charset="utf-8">
<title>Walsh &amp; Brand Pty Ltd — Business Card</title>
<link rel="stylesheet" href="https://fonts.googleapis.com/css2?family=Cinzel:wght@400;600&display=swap">
<style>
  :root {
    --ink: #000000;
    --paper: #fbfbfb;
    --charcoal: #333333;
    --grey: #959595;
    --backdrop: #e6e6e6;
  }
  * { margin: 0; padding: 0; box-sizing: border-box; }
  html, body {
    width: 1200px; height: 913px; overflow: hidden;
    background: var(--backdrop);
    font-family: "Cinzel", serif;
  }
  .canvas {
    position: relative; width: 1200px; height: 913px;
    display: flex; align-items: center; justify-content: center; gap: 48px;
  }
  .card {
    position: relative; width: 520px; height: 318px; overflow: hidden;
    box-shadow: 0 10px 28px rgba(0,0,0,.22);
  }

  /* Front */
  .card--front { background: var(--paper); color: var(--charcoal); }
  .front__accent { position: absolute; inset: 0; width: 100%; height: 100%; }
  .brand {
    position: absolute; left: 34px; top: 58px;
    display: flex; flex-direction: column; gap: 14px;
  }
  .brand__mark { width: 62px; height: 62px; background: var(--grey); }
  .brand__name {
    font-size: 14px; font-weight: 400; letter-spacing: .08em;
    color: var(--grey); text-transform: uppercase;
  }
  .agents {
    position: absolute; right: 92px; top: 40px; text-align: right;
  }
  .agents__names {
    font-size: 19px; font-weight: 400; color: var(--ink); letter-spacing: .02em;
  }
  .agents__role {
    font-size: 11px; color: var(--grey); letter-spacing: .06em; margin-top: 2px;
  }
  .contact {
    position: absolute; right: 22px; top: 100px;
    list-style: none; text-align: right;
    font-size: 11px; color: var(--ink); line-height: 19px;
  }
  .contact li { display: flex; align-items: center; justify-content: flex-end; gap: 6px; }
  .contact svg { width: 10px; height: 10px; fill: var(--grey); }
  .address {
    position: absolute; left: 34px; bottom: 34px;
    font-style: normal; color: var(--ink);
  }
  .address__street { font-size: 12px; letter-spacing: .03em; }
  .address__locality { font-size: 15px; font-weight: 600; letter-spacing: .02em; }

  /* Back */
  .card--back {
    background: linear-gradient(155deg, #1c1c1c 0%, var(--ink) 45%, #111 100%);
    display: flex; flex-direction: column; align-items: center; justify-content: center; gap: 22px;
  }
  .card--back .brand__mark { width: 96px; height: 96px; background: var(--grey); }
  .card--back .brand__name { font-size: 18px; color: var(--grey); letter-spacing: .12em; }
</style>
</head>
<body>
<main class="canvas">

  <section class="card card--front" aria-label="Business card front">
    <svg class="front__accent" viewBox="0 0 520 318" aria-hidden="true">
      <circle cx="520" cy="22" r="16" fill="#cfcfcf"/>
      <path d="M420 318 C420 230 455 178 520 172 L520 318 Z" fill="#000"/>
    </svg>

    <div class="brand">
      <div class="brand__mark"></div>
      <p class="brand__name">Walsh &amp; Brand Pty Ltd.</p>
    </div>

    <div class="agents">
      <h1 class="agents__names">Owen Walsh &amp; Lucy Brand</h1>
      <p class="agents__role">Sales Agents &amp; Onsite Manager</p>
    </div>

    <ul class="contact">
      <li>07 5948 2063
        <svg viewBox="0 0 10 10" aria-label="Phone"><path d="M2 0.5 L4 2.5 L3 3.8 Q4.3 5.8 6.2 7 L7.5 6 L9.5 8 L8 9.5 Q3.5 9 0.5 2 Z"/></svg></li>
      <li>07 5948 2174
        <svg viewBox="0 0 10 10" aria-label="Fax"><rect x="2" y="0.5" width="6" height="3"/><rect x="0.5" y="4" width="9" height="5" rx="1"/></svg></li>
      <li>0431 857 219
        <svg viewBox="0 0 10 10" aria-label="Mobile"><rect x="2.5" y="0.5" width="5" height="9" rx="1"/></svg></li>
    </ul>

    <address class="address">
      <p class="address__street">3/42 Marlow Crescent,</p>
      <p class="address__locality">FERNLEA QLD 4213</p>
    </address>
  </section>

  <section class="card card--back" aria-label="Business card back">
    <div class="brand__mark"></div>
    <p class="brand__name">Walsh &amp; Brand Pty Ltd.</p>
  </section>

</main>
</body>
</html>
```